Business card design for international hub site

I need a business card design with the logo attached. Although the site is for the teenage audience (it is about the high school graduation ball, the Prom), the business card is for professional use to be given to professional contacts (B2B), such as suppliers and partners, so it needs to look professional (but also girly, glamours and clean).

Target Market(s)

B2B

Industry/Entity Type

Media

Colors
eea4c8
f9d9e8
e667a6
9d9d9d
1b1b1b

Requirements
Must have
• Space for Name, Tile, Address, Phone, email and website.
Should not have
• Photo

```html
<!DOCTYPE html>
<html lang="en">
<head>
<meta charset="utf-8">
<title>Gala Whirl – Business Card</title>
<link rel="stylesheet" href="https://fonts.googleapis.com/css2?family=Arimo:wght@400;700&display=swap">
<style>
  :root {
    --pink-deep: #e0247f;
    --pink-mid: #e667a6;
    --pink-soft: #eea4c8;
    --pink-pale: #f9d9e8;
    --grey: #9d9d9d;
    --ink: #1b1b1b;
    --white: #ffffff;
    --backdrop: #2a2a2a;
  }
  * { box-sizing: border-box; margin: 0; padding: 0; }
  html, body {
    width: 1200px; height: 997px; overflow: hidden;
    background: var(--backdrop);
    font-family: "Arimo", Arial, sans-serif;
  }
  .canvas {
    position: relative; width: 1200px; height: 997px;
    display: flex; flex-direction: column; align-items: center;
    justify-content: center; gap: 56px;
  }
  .card {
    position: relative; width: 700px; height: 400px;
    border-radius: 26px; overflow: hidden;
    box-shadow: 0 18px 40px rgba(0,0,0,.5);
  }
  .card__art { position: absolute; inset: 0; }

  /* Front */
  .card--front .card__art {
    background: linear-gradient(115deg, var(--pink-deep) 0%, var(--pink-mid) 28%, var(--pink-pale) 50%, var(--white) 62%, var(--pink-soft) 82%, var(--pink-mid) 100%);
  }
  .brand {
    position: absolute; left: 50%; top: 50%;
    transform: translate(-50%, -50%);
    display: flex; align-items: center; gap: 14px;
    font-size: 52px; font-weight: 400; letter-spacing: 1px;
    white-space: nowrap;
  }
  .brand__dot { width: 16px; height: 16px; border-radius: 50%; }
  .card--front .brand { color: var(--grey); }
  .card--front .brand__dot { background: var(--pink-mid); }

  /* Back */
  .card--back .card__art {
    background: radial-gradient(ellipse at 45% 30%, var(--pink-mid) 0%, var(--pink-deep) 55%, #c81a6e 100%);
  }
  .card--back .brand { top: 30%; left: 46%; color: var(--white); font-size: 44px; }
  .card--back .brand__dot { background: var(--white); width: 13px; height: 13px; }

  .person {
    position: absolute; right: 44px; top: 190px; text-align: right; color: var(--white);
  }
  .person__name { font-size: 22px; font-weight: 700; letter-spacing: .5px; }
  .person__title { font-size: 14px; margin-top: 4px; }
  .person__web { font-size: 17px; font-weight: 700; margin-top: 16px; }

  .contact {
    position: absolute; left: 40px; bottom: 34px; list-style: none;
    color: var(--white); font-size: 16px; line-height: 1.25;
  }
  .contact li { display: flex; align-items: flex-start; gap: 10px; margin-top: 7px; }
  .contact svg { flex: none; width: 18px; height: 18px; margin-top: 1px; }
</style>
</head>
<body>
<main class="canvas">
  <section class="card card--front">
    <div class="card__art" role="img" aria-label="Pink and white swirl flourishes with pearl-dot strands"></div>
    <div class="brand"><span class="brand__dot"></span>gala whirl</div>
  </section>

  <section class="card card--back">
    <div class="card__art" role="img" aria-label="Hot pink glitter texture with sparkling bokeh"></div>
    <div class="brand"><span class="brand__dot"></span>gala whirl</div>

    <div class="person">
      <p class="person__name">LENA MARSH</p>
      <p class="person__title">Marketing Director</p>
      <p class="person__web">www.halcyonreach.com</p>
    </div>

    <ul class="contact">
      <li>
        <svg viewBox="0 0 18 18"><circle cx="9" cy="9" r="9" fill="#fff"/><path d="M6 5l2 2-1 1.2c.6 1.3 1.5 2.2 2.8 2.8L11 10l2 2-1.2 1.3C8.5 13 5 9.5 4.7 6.2z" fill="#e0247f"/></svg>
        (555) 014-2290
      </li>
      <li>
        <svg viewBox="0 0 18 18"><circle cx="9" cy="9" r="9" fill="#fff"/><path d="M6 5l2 2-1 1.2c.6 1.3 1.5 2.2 2.8 2.8L11 10l2 2-1.2 1.3C8.5 13 5 9.5 4.7 6.2z" fill="#e0247f"/></svg>
        (555) 018-3361
      </li>
      <li>
        <svg viewBox="0 0 18 18"><circle cx="9" cy="9" r="9" fill="#fff"/><rect x="4.5" y="6" width="9" height="6.5" rx="1" fill="#e0247f"/><path d="M4.8 6.4L9 9.6l4.2-3.2" stroke="#fff" stroke-width="1" fill="none"/></svg>
        lmarsh@halcyonreach.com
      </li>
      <li>
        <svg viewBox="0 0 18 18"><circle cx="9" cy="9" r="9" fill="#fff"/><path d="M9 3.8a3.4 3.4 0 0 0-3.4 3.4C5.6 10 9 14 9 14s3.4-4 3.4-6.8A3.4 3.4 0 0 0 9 3.8z" fill="#e0247f"/><circle cx="9" cy="7.2" r="1.2" fill="#fff"/></svg>
        <span>48 Orchard Row, 2nd Floor<br>Maple Hill, GA 30100</span>
      </li>
    </ul>
  </section>
</main>
</body>
</html>
```